Business Card for Professional Photographer

I'm looking for an eye catching modern clean design that compliments my logo/ website fonts & colours.
I specialise in architecture, corporate & commercial photography so I'm marketing to professional clients rather than portrait / wedding clients.

I would prefer to not have a solid black design.

My logo brand guide is as follows :

Main front font. : Reislust
Main font colour : #fff
Slogan front font : Ubuntu Bold
Monogram front font : Venti Medium
Container colour : #fff

I need print ready files in pdf .png & .eps formats.

Included in the files below are some screen grabs as reference to font & colours etc.

```html
<!DOCTYPE html>
<html lang="en">
<head>
<meta charset="utf-8">
<title>Clear Aperture – Business Card</title>
<link rel="stylesheet" href="https://fonts.googleapis.com/css2?family=Montserrat:wght@300;400;500;600;700&display=swap">
<style>
  :root{
    --bg:#5f6062;
    --card-black:#151515;
    --gold:#c9a14a;
    --gold-light:#f6e6a6;
    --gold-deep:#b8893a;
    --white:#ffffff;
    --grey-text:#b9b9b9;
    --photo-sky:#b8cde4;
    --photo-ground:#c7c7c5;
    --ink:#4a4a4a;
  }
  *{margin:0;padding:0;box-sizing:border-box}
  html,body{width:1200px;height:960px;overflow:hidden}
  body{background:var(--bg);font-family:"Montserrat",sans-serif;position:relative}

  .card{position:absolute;left:250px;width:700px;height:400px;border-radius:28px;overflow:hidden}
  .card--front{top:50px}
  .card--back{top:510px;background:var(--card-black)}

  /* front */
  .front-photo{position:absolute;inset:0;
    background:linear-gradient(180deg,var(--photo-sky) 0%,#dfe6ee 45%,#d9d9d6 60%,var(--photo-ground) 100%)}
  .front-veil{position:absolute;inset:0;background:rgba(255,255,255,.35)}
  .front-brand{position:absolute;left:150px;top:160px;display:flex;align-items:center;gap:22px}
  .brand-square{width:74px;height:74px;border:4px solid var(--gold);border-radius:6px;flex:none}
  .brand-name{font-weight:400;font-size:30px;letter-spacing:6px;text-transform:uppercase;line-height:1;white-space:nowrap}
  .front-brand .brand-name{color:var(--ink)}
  .brand-tagline{font-weight:600;font-size:10px;letter-spacing:2.5px;color:var(--gold);margin-top:8px;white-space:nowrap}
  .front-brand .brand-tagline{color:#7a6a45}

  /* back */
  .back-brand{position:absolute;left:50px;top:56px;display:flex;align-items:center;gap:20px}
  .back-brand .brand-name{color:var(--white);font-size:28px;letter-spacing:5px}
  .holder{position:absolute;left:80px;top:196px}
  .holder-name{font-weight:700;font-size:22px;line-height:28px;color:var(--gold);letter-spacing:.5px}
  .holder-title{font-weight:500;font-size:16px;line-height:22px;color:var(--white);margin-top:2px}
  .holder-address{font-weight:400;font-size:15px;color:var(--grey-text);margin-top:8px;line-height:20px}

  .contacts{position:absolute;right:44px;top:166px;list-style:none;text-align:right}
  .contacts li{font-size:15px;color:var(--grey-text);line-height:26px;display:flex;justify-content:flex-end;align-items:center;gap:10px;white-space:nowrap}
  .contacts svg{width:14px;height:14px;fill:var(--gold);flex:none}

  .band{position:absolute;left:0;right:60px;top:330px;height:44px;
    background:linear-gradient(90deg,var(--gold-deep) 0%,var(--gold) 25%,var(--gold-light) 60%,var(--gold) 85%,var(--gold-deep) 100%)}
  .band-web{position:absolute;left:80px;top:12px;font-size:16px;font-weight:500;color:#1d1d1d;letter-spacing:.3px}
  .band-end{position:absolute;right:0;top:310px;width:60px;height:64px;background:#8b8b8b;display:flex;align-items:center;justify-content:center}
  .band-end span{width:28px;height:28px;border:3px solid #1d1d1d;border-radius:4px}
</style>
</head>
<body>

<section class="card card--front">
  <div class="front-photo" role="img" aria-label="Photograph of a modern white and orange building with a car park under a cloudy blue sky"></div>
  <div class="front-veil"></div>
  <div class="front-brand">
    <span class="brand-square"></span>
    <div>
      <div class="brand-name">Clear Aperture</div>
      <div class="brand-tagline">Architecture Corporate Commercial</div>
    </div>
  </div>
</section>

<section class="card card--back">
  <div class="back-brand">
    <span class="brand-square"></span>
    <div>
      <div class="brand-name">Clear Aperture</div>
      <div class="brand-tagline">Architecture Corporate Commercial</div>
    </div>
  </div>

  <ul class="contacts">
    <li>555-014-2286
      <svg viewBox="0 0 24 24"><path d="M6.6 10.8a15 15 0 0 0 6.6 6.6l2.2-2.2a1 1 0 0 1 1-.25 11.4 11.4 0 0 0 3.6.57 1 1 0 0 1 1 1V20a1 1 0 0 1-1 1A17 17 0 0 1 3 4a1 1 0 0 1 1-1h3.5a1 1 0 0 1 1 1c0 1.25.2 2.45.57 3.57a1 1 0 0 1-.25 1z"/></svg></li>
    <li>555-019-7431
      <svg viewBox="0 0 24 24"><path d="M7 1h10a2 2 0 0 1 2 2v18a2 2 0 0 1-2 2H7a2 2 0 0 1-2-2V3a2 2 0 0 1 2-2zm0 3v14h10V4z"/></svg></li>
    <li>555-013-6092
      <svg viewBox="0 0 24 24"><path d="M6 2h10v5H6zM4 8h16a2 2 0 0 1 2 2v7h-4v5H6v-5H2v-7a2 2 0 0 1 2-2zm4 9v3h8v-3z"/></svg></li>
    <li>info@clearaperture.com
      <svg viewBox="0 0 24 24"><path d="M2 5h20v14H2zm2 2v.5l8 5 8-5V7z"/></svg></li>
  </ul>

  <div class="holder">
    <div class="holder-name">DANIEL REEVE</div>
    <div class="holder-title">President</div>
    <div class="holder-address">2140 Alder Ridge Road<br>Juneau, Alaska 99801</div>
  </div>

  <div class="band"><span class="band-web">www.clearaperture.com</span></div>
  <div class="band-end"><span></span></div>
</section>

</body>
</html>
```